Design a poster that illustrates the six central pillars of our school district's efforts with students. The attached PDF outlines the six main competencies we aim for students to possess upon graduation. Each of the 6 has 3 bullet points for the poster as well. The title is "Profile of a Trailblazer". Our mascot is this attached winged wheel. The overall concept is that staff take kids when they are young and develop these 6 things when they graduate. Our colors are navy, red, and white. We will make this poster in a variety of sizes in offices, classrooms, and in digital spaces as well. On the PDF - ignore the column that says "Synthesis". That has nothing to do with this poster.

The district is Harlow Creek Public Schools https://www.harlowcreek-schools.example/

```html
<!DOCTYPE html>
<html lang="en">
<head>
<meta charset="utf-8">
<title>Profile of a Trailblazer — Harlow Creek Public Schools</title>
<link rel="stylesheet" href="https://fonts.googleapis.com/css2?family=Archivo+Black&family=Oswald:wght@500;600&display=swap">
<style>
  :root {
    --navy: #0c0c3c;
    --red: #a01c24;
    --white: #ffffff;
    --backdrop: #bfc0c2;
  }
  * { box-sizing: border-box; margin: 0; padding: 0; }
  html, body { width: 924px; height: 1200px; overflow: hidden; background: var(--backdrop); }
  .poster {
    position: absolute; left: 90px; top: 74px; width: 744px; height: 1052px;
    background: var(--navy);
  }
  .masthead {
    position: absolute; left: 0; top: 0; width: 744px; height: 185px;
    background: var(--white); border-bottom: 7px solid var(--red);
  }
  .district-mark {
    position: absolute; left: 62px; top: 58px; width: 230px;
    display: flex; align-items: center; gap: 10px;
    font-family: "Oswald", sans-serif; font-weight: 600; font-size: 22px; line-height: 1.1;
    color: var(--navy); text-transform: uppercase;
  }
  .district-mark .dot { flex: none; width: 26px; height: 26px; border-radius: 50%; background: var(--red); }
  .title {
    position: absolute; left: 300px; top: 68px;
    font-family: "Archivo Black", sans-serif; line-height: 1; letter-spacing: -0.5px;
  }
  .title .kicker { display: block; color: var(--red); font-size: 40px; }
  .title .main { display: block; color: var(--navy); font-size: 47px; margin-top: 4px; }
  .pillar {
    position: absolute; width: 313px; height: 224px;
    border: 3px solid var(--red); border-radius: 14px;
  }
  .pillar h2 {
    position: absolute; left: 16px; top: -22px; padding: 0 6px;
    background: var(--navy); color: var(--white);
    font-family: "Oswald", sans-serif; font-weight: 600; font-size: 27px; line-height: 38px;
  }
  .pillar ul {
    list-style: none; position: absolute; left: 20px; right: 6px; top: 24px;
    font-family: "Oswald", sans-serif; font-weight: 500; font-size: 18.5px; line-height: 23px;
    color: var(--white); letter-spacing: -0.4px;
  }
  .pillar li { position: relative; padding-left: 10px; margin-bottom: 14px; }
  .pillar li::before {
    content: ""; position: absolute; left: -1px; top: 9px;
    width: 5px; height: 5px; border-radius: 50%; background: var(--white);
  }
  .col-left { left: 55px; }
  .col-right { left: 399px; }
  .row-1 { top: 231px; }
  .row-2 { top: 509px; }
  .row-3 { top: 785px; }
  .pillar.spacious li { margin-bottom: 22px; }
  .pillar.compact ul { top: 20px; line-height: 22px; }
  .pillar.compact li { margin-bottom: 9px; }
  .pillar.compact li::before { top: 8px; }
</style>
</head>
<body>
  <main class="poster">
    <header class="masthead">
      <div class="district-mark"><span class="dot"></span><span>Harlow Creek Public Schools</span></div>
      <h1 class="title"><span class="kicker">PROFILE OF A</span><span class="main">TRAILBLAZER</span></h1>
    </header>

    <section class="pillar col-left row-1">
      <h2>Communicator</h2>
      <ul>
        <li>Expresses ideas clearly and respectfully (written &amp; verbal).</li>
        <li>Listens actively and understands diverse perspectives.</li>
        <li>Adjusts communication to suit the audience and context.</li>
      </ul>
    </section>

    <section class="pillar col-right row-1">
      <h2>Critical Thinker</h2>
      <ul>
        <li>Questions, analyzes, and evaluates information from multiple sources.</li>
        <li>Identifies and solves complex problems creatively.</li>
        <li>Uses evidence and diverse perspectives to form reasoned conclusions and make informed</li>
      </ul>
    </section>

    <section class="pillar col-left row-2 spacious">
      <h2>Responsible</h2>
      <ul>
        <li>Takes ownership of actions, choices, and commitments.</li>
        <li>Manages time, resources, and self to meet expectations.</li>
        <li>Acts with integrity and advocates for self and others.</li>
      </ul>
    </section>

    <section class="pillar col-right row-2 compact">
      <h2>Adaptable</h2>
      <ul>
        <li>Responds productively to new situations, challenges, and feedback.</li>
        <li>Learns from new experiences and applies prior knowledge in evolving contexts.</li>
        <li>Adjusts behavior and approach to effectively engage with diverse groups and environments.</li>
      </ul>
    </section>

    <section class="pillar col-left row-3">
      <h2>Collaborator</h2>
      <ul>
        <li>Contributes effectively and cooperatively to shared goals</li>
        <li>Listens actively and values diverse ideas and perspectives.</li>
        <li>Engages respectfully, compromising and leading when appropriate.</li>
      </ul>
    </section>

    <section class="pillar col-right row-3 compact">
      <h2>Compassionate</h2>
      <ul>
        <li>Understands and acknowledges others' feelings, perspectives, and experiences.</li>
        <li>Responds with kindness, patience, and support.</li>
        <li>Seeks to connect with and contribute positively to the well-being of others</li>
      </ul>
    </section>
  </main>
</body>
</html>
```